App Design Project

Hello,
I'm looking for a great designer for my iOS Applications, we have a lot of works and we're short in designers :(
I want to revamp my thermometer iOS app. You will find attached the images I want to replace. I need something with the same element (temp, condition, weather icon) but with a different look!
Same, new icon, you have carte blanche to this one.
I want a design that stands out from the hundreds of weather application that almost all the same design. I am looking for something that does say "wow, it rocks."
Please do not Provide classic design that we can see everywhere ... I'm looking for something with a real artistic choice, contrast, colours, etc.
As a marketing screenshot, I want something classic, you'll find an example attached, feel free to innovate.
To sum-up :
- One new view for my App
- One new icon
- One marketing screenshot
Marketing

```html
<!DOCTYPE html>
<html lang="en">
<head>
<meta charset="utf-8">
<title>Weather App Screen</title>
<link rel="stylesheet" href="https://fonts.googleapis.com/css2?family=Roboto:wght@100;300;400;500&display=swap">
<style>
  :root {
    --page-bg: #f3f4f6;
    --sky-top: #5cc4f2;
    --sky-mid: #2f9fe0;
    --sky-low: #1f86cf;
    --band-top: #1b7fca;
    --band-low: #0f6bb6;
    --band-line: rgba(255, 255, 255, 0.35);
    --ink-white: #ffffff;
    --ink-soft: rgba(255, 255, 255, 0.75);
    --ink-grey: #e6ecf1;
    --toggle-light: #eef2f5;
    --toggle-blue: #2a8fd8;
    --icon-light: #f4f6f8;
    --icon-dark: #bcc6cf;
  }
  * { margin: 0; padding: 0; box-sizing: border-box; }
  html, body {
    width: 1200px;
    height: 1000px;
    overflow: hidden;
    background: var(--page-bg);
    font-family: "Roboto", "Helvetica Neue", Arial, sans-serif;
  }
  .app-screen {
    position: absolute;
    left: 340px;
    top: 38px;
    width: 520px;
    height: 924px;
    overflow: hidden;
    background: linear-gradient(180deg, var(--sky-top) 0%, var(--sky-mid) 45%, var(--sky-low) 72%);
    box-shadow: 0 10px 30px rgba(0, 40, 80, 0.18);
  }
  .app-screen::before {
    content: "";
    position: absolute;
    inset: 0;
    background: linear-gradient(115deg, rgba(255,255,255,0.14) 0%, rgba(255,255,255,0.06) 48%, rgba(255,255,255,0) 48.2%);
    pointer-events: none;
  }
  .temperature {
    position: absolute;
    left: 72px;
    top: 52px;
    font-weight: 100;
    font-size: 272px;
    line-height: 1;
    color: var(--ink-white);
    letter-spacing: -6px;
  }
  .temperature-degree {
    position: absolute;
    left: 364px;
    top: 50px;
    width: 28px;
    height: 28px;
    border: 3px solid var(--ink-white);
    border-radius: 50%;
  }
  .unit-toggle {
    position: absolute;
    left: 404px;
    top: 114px;
    width: 46px;
    height: 102px;
    border-radius: 6px;
    overflow: hidden;
    box-shadow: 0 2px 5px rgba(0, 50, 100, 0.3);
    font-weight: 500;
    font-size: 36px;
    text-align: center;
  }
  .unit-option { display: block; height: 51px; line-height: 51px; }
  .unit-option--active { background: var(--toggle-light); color: var(--toggle-blue); }
  .unit-option--idle { background: var(--toggle-blue); color: var(--ink-white); border-top: 1px solid rgba(255,255,255,0.5); }
  .condition-art {
    position: absolute;
    left: 182px;
    top: 368px;
    width: 156px;
    height: 156px;
    border-radius: 24px;
    background: linear-gradient(180deg, var(--icon-light) 0%, var(--icon-dark) 100%);
    opacity: 0.9;
  }
  .condition-label {
    position: absolute;
    left: 0;
    width: 100%;
    top: 558px;
    text-align: center;
    font-weight: 300;
    font-size: 42px;
    color: var(--ink-grey);
    letter-spacing: 1px;
  }
  .stats-band {
    position: absolute;
    left: 0;
    top: 660px;
    width: 100%;
    height: 264px;
    background: linear-gradient(180deg, var(--band-top) 0%, var(--band-top) 68%, var(--band-low) 68.2%, var(--band-low) 100%);
    border-top: 2px solid var(--band-line);
  }
  .stat {
    position: absolute;
    top: 18px;
    display: flex;
    align-items: flex-start;
    color: var(--ink-white);
  }
  .stat-main { display: flex; flex-direction: column; align-items: center; }
  .stat-value { font-weight: 100; font-size: 112px; line-height: 1; letter-spacing: -3px; }
  .stat-prefix { font-weight: 300; font-size: 38px; margin-top: 14px; margin-right: 6px; }
  .stat-unit { font-weight: 300; font-size: 28px; margin-top: 8px; margin-left: 8px; }
  .stat-label {
    margin-top: 6px;
    font-weight: 300;
    font-size: 14px;
    color: var(--ink-soft);
    letter-spacing: 1px;
  }
  .stat--wind { left: 40px; }
  .stat--humidity { left: 310px; }
  .info-button {
    position: absolute;
    right: 30px;
    bottom: 16px;
    width: 22px;
    height: 22px;
  }
</style>
</head>
<body>
  <main class="app-screen">
    <div class="temperature">23</div>
    <div class="temperature-degree"></div>
    <div class="unit-toggle">
      <span class="unit-option unit-option--active">C</span>
      <span class="unit-option unit-option--idle">F</span>
    </div>

    <div class="condition-art" role="img" aria-label="Weather condition illustration: sun"></div>

    <div class="condition-label">SUNNY</div>

    <section class="stats-band">
      <div class="stat stat--wind">
        <span class="stat-prefix">N</span>
        <div class="stat-main">
          <div class="stat-value">39</div>
          <div class="stat-label">WIND</div>
        </div>
        <span class="stat-unit">km/h</span>
      </div>
      <div class="stat stat--humidity">
        <div class="stat-main">
          <div class="stat-value">30</div>
          <div class="stat-label">HUMIDITY</div>
        </div>
        <span class="stat-unit">%</span>
      </div>
      <svg class="info-button" viewBox="0 0 22 22" aria-label="Info">
        <circle cx="11" cy="11" r="10" fill="none" stroke="rgba(255,255,255,0.7)" stroke-width="1.5"/>
        <circle cx="11" cy="6.5" r="1.4" fill="rgba(255,255,255,0.85)"/>
        <rect x="9.9" y="9.5" width="2.2" height="7" fill="rgba(255,255,255,0.85)"/>
      </svg>
    </section>
  </main>
</body>
</html>
```